RESIDENTIAL CONSTRUCTION

We are a company that specializes in building custom residential homes, the design should also emphasize that quality and service is our priority.

Industry/Entity Type

Construction Company

Contact Information for Business Card

Contact Person: Marcus Lindqvist
Company Address: 273 West Alder Ave San Jose , Ca 95380
Phone Number : 408-731-2946
Email Address: Stoneridgehomes517@mailvista.net

Font styles to use
Sans Serif

Colors
ec1f27

Requirements
Must have
• CSLB # 7362015
Nice to have
• needs to have same color as logo i uploaded, we will be printing these on a clear plastic card.

```html
<!DOCTYPE html>
<html lang="en">
<head>
<meta charset="utf-8">
<title>Stoneridge General Builders – Business Card</title>
<link rel="stylesheet" href="https://fonts.googleapis.com/css2?family=Oswald:wght@500&family=Roboto:wght@300;400&display=swap">
<style>
  :root {
    --brand-red: #c11f30;
    --brand-red-light: #cf4454;
    --card-white: #ffffff;
    --text-grey: #8a8a8a;
    --backdrop: #e9e7e4;
  }
  * { box-sizing: border-box; margin: 0; padding: 0; }
  html, body {
    width: 1200px;
    height: 950px;
    overflow: hidden;
    background: var(--backdrop);
  }
  .canvas {
    width: 1200px;
    height: 950px;
    display: flex;
    align-items: center;
    justify-content: center;
  }
  .business-card {
    position: relative;
    width: 1050px;
    height: 600px;
    background: var(--card-white);
    box-shadow: 0 6px 24px rgba(0,0,0,0.12);
    overflow: hidden;
  }
  .brand {
    position: absolute;
    top: 70px;
    left: 470px;
    display: flex;
    align-items: center;
    gap: 18px;
  }
  .brand-square {
    width: 58px;
    height: 58px;
    background: var(--brand-red);
  }
  .brand-name {
    font-family: "Oswald", sans-serif;
    font-weight: 500;
    color: var(--brand-red);
    text-transform: uppercase;
    line-height: 1;
  }
  .brand-name .line-main { display: block; font-size: 64px; letter-spacing: 1px; }
  .brand-name .line-sub { display: block; font-size: 22px; letter-spacing: 7px; margin-top: 6px; }

  .contact-person {
    position: absolute;
    left: 70px;
    top: 300px;
  }
  .person-name {
    font-family: "Oswald", sans-serif;
    font-weight: 500;
    font-size: 38px;
    color: var(--brand-red);
    text-transform: uppercase;
    letter-spacing: 0.5px;
    margin-bottom: 10px;
  }
  .address-line {
    font-family: "Roboto", sans-serif;
    font-weight: 300;
    font-size: 25px;
    line-height: 1.4;
    color: var(--text-grey);
  }

  .contact-band {
    position: absolute;
    left: 0;
    right: 0;
    top: 478px;
    height: 54px;
    background: var(--brand-red);
    display: flex;
    align-items: center;
  }
  .contact-band .band-lead {
    width: 58px;
    height: 100%;
    background: var(--brand-red-light);
  }
  .contact-band p {
    font-family: "Roboto", sans-serif;
    font-weight: 400;
    font-size: 23px;
    color: var(--card-white);
    padding-left: 10px;
    white-space: nowrap;
  }
  .contact-band strong { font-weight: 400; }
  .edge-band {
    position: absolute;
    left: 0;
    right: 0;
    bottom: 0;
    height: 36px;
    background: var(--brand-red);
  }
</style>
</head>
<body>
<main class="canvas">
  <section class="business-card">
    <div class="brand">
      <div class="brand-square"></div>
      <div class="brand-name">
        <span class="line-main">Stoneridge</span>
        <span class="line-sub">General Builders</span>
      </div>
    </div>

    <div class="contact-person">
      <h1 class="person-name">Marcus Lindqvist</h1>
      <p class="address-line">273 West Alder Ave San Jose</p>
      <p class="address-line">Ca 95380</p>
      <p class="address-line">CSLB # 7362015</p>
    </div>

    <div class="contact-band">
      <span class="band-lead"></span>
      <p><strong>P:</strong> 408-731-2946 &nbsp;<strong>E:</strong> Stoneridgehomes517@mailvista.net</p>
    </div>
    <div class="edge-band"></div>
  </section>
</main>
</body>
</html>
```